business card deign

Logo needs the following on it.
1. attached logo
2. Tagline - "If it keeps the cooler full or the crowd moving...count on us!"
3. Name- Dalton Pikes, Founder and CPO
4. Address - 412 E. Carver Avenue, Ste 2207, Tampa, FL. 33917
5. Phone - 555.318.4726

```html
<!DOCTYPE html>
<html lang="en">
<head>
<meta charset="utf-8">
<title>Hopwell Business Card</title>
<link href="https://fonts.googleapis.com/css2?family=Montserrat:wght@400;500;700;800&display=swap" rel="stylesheet">
<style>
  :root {
    --page: #e9e6e1;
    --ink: #141414;
    --paper: #ffffff;
    --band: #1a1a1a;
    --stripe: #a9a9a9;
    --shadow: rgba(0,0,0,0.25);
  }
  * { margin: 0; padding: 0; box-sizing: border-box; }
  html, body { width: 1200px; height: 931px; overflow: hidden; }
  body {
    background: var(--page);
    font-family: "Montserrat", Arial, sans-serif;
    position: relative;
  }
  .card {
    position: absolute;
    width: 560px;
    height: 320px;
    box-shadow: 0 14px 30px var(--shadow);
    overflow: hidden;
  }
  .card-back { left: 140px; top: 110px; background: var(--ink); }
  .card-front { left: 500px; top: 490px; background: var(--paper); }

  .pattern-area {
    position: absolute; inset: 0;
    background: linear-gradient(120deg, #d8d8d8 0%, #6a6a6a 22%, #262626 45%, #111 70%, #0b0b0b 100%);
    opacity: 0.55;
  }
  .back-brand {
    position: absolute; left: 0; right: 0; top: 132px;
    display: flex; justify-content: center; align-items: center; gap: 14px;
    color: var(--paper);
  }
  .brand-square { width: 22px; height: 22px; background: currentColor; }
  .brand-name { font-weight: 800; font-size: 40px; letter-spacing: 12px; }

  .front-brand {
    position: absolute; left: 30px; top: 140px;
    display: flex; align-items: center; gap: 10px; color: var(--ink);
  }
  .front-brand .brand-name { font-size: 25px; letter-spacing: 6px; }
  .front-brand .brand-square { width: 15px; height: 15px; }

  .divider {
    position: absolute; left: 262px; top: 58px;
    width: 1.5px; height: 124px; background: var(--ink);
  }
  .contact { position: absolute; left: 282px; top: 54px; color: var(--ink); }
  .contact-name { font-weight: 800; font-size: 18px; letter-spacing: 0.5px; }
  .contact-title { font-size: 14px; margin-top: 2px; }
  .contact-list { list-style: none; margin-top: 12px; font-size: 13px; line-height: 1.35; }
  .contact-list li { display: flex; gap: 8px; align-items: flex-start; }
  .contact-list svg { width: 14px; height: 14px; flex: none; margin-top: 2px; }

  .wave { position: absolute; left: 0; top: 0; }
  .tagline { font-family: "Montserrat", Arial, sans-serif; font-size: 12px; font-weight: 500; fill: var(--paper); }
</style>
</head>
<body>

<section class="card card-back">
  <div class="pattern-area" role="img" aria-label="Repeating pattern of the brand symbol fading from silver to black"></div>
  <div class="back-brand">
    <span class="brand-square"></span>
    <span class="brand-name">HOPWELL</span>
  </div>
</section>

<section class="card card-front">
  <svg class="wave" width="560" height="320" viewBox="0 0 560 320">
    <path d="M0,298 C200,298 330,206 560,190 L560,204 C340,218 200,305 0,305 Z" fill="var(--stripe)"/>
    <path d="M0,308 C200,308 340,226 560,210 L560,320 L0,320 Z" fill="var(--band)"/>
    <path id="tagline-path" d="M100,315 C250,304 380,252 552,236" fill="none"/>
    <text class="tagline"><textPath href="#tagline-path">If it keeps the cooler full or the crowd moving...count on us!</textPath></text>
  </svg>

  <div class="front-brand">
    <span class="brand-square"></span>
    <span class="brand-name">HOPWELL</span>
  </div>

  <div class="divider"></div>

  <div class="contact">
    <div class="contact-name">DALTON PIKES</div>
    <div class="contact-title">Founder and CPO</div>
    <ul class="contact-list">
      <li>
        <svg viewBox="0 0 24 24" aria-hidden="true"><path fill="currentColor" d="M6.6 10.8a15.1 15.1 0 0 0 6.6 6.6l2.2-2.2c.3-.3.7-.4 1-.2 1.1.4 2.300.6 3.6.6.6 0 1 .4 1 1V20c0 .6-.4 1-1 1A17 17 0 0 1 3 4c0-.6.4-1 1-1h3.5c.6 0 1 .4 1 1 0 1.3.2 2.5.6 3.6.1.3 0 .7-.2 1z"/></svg>
        <span>555.318.4726</span>
      </li>
      <li>
        <svg viewBox="0 0 24 24" aria-hidden="true"><path fill="currentColor" d="M12 2a7 7 0 0 0-7 7c0 5.2 7 13 7 13s7-7.8 7-13a7 7 0 0 0-7-7zm0 9.5A2.5 2.5 0 1 1 12 6.5a2.5 2.5 0 0 1 0 5z"/></svg>
        <span>412 E. Carver Avenue, Ste 2207,<br>Tampa, FL. 33917</span>
      </li>
    </ul>
  </div>
</section>

</body>
</html>
```